We are a local Communty Pharmacy wishing to promote and market a specialised Pharmaceutical Service

We would like a design that is professional and enticing ( according to the brief In attached files)
We wish to Market Compounding Pharmacy as a specialist side of our business.
We have the expertise a purpose built preparation laboratory.
The main purpose is an Internet presence that entices prospective patients to contact or visit our physical store.

Target Market(s)

Patients Medicos and Veterinary clients

Industry/Entity Type

Pharmacy

Coding

Coded - Design and coding required

Number of Pages Required

1 page

Requirements
Must have
• Clear friendly image
Nice to have
• soft enticing feel
Should not have
• No crass loud unprofessional elements

```html
<!DOCTYPE html>
<html lang="en">
<head>
<meta charset="utf-8">
<title>Kestrel Compounding Pharmacy</title>
<link href="https://fonts.googleapis.com/css2?family=Roboto:ital,wght@0,300;0,400;0,500;0,700;1,400&family=Oswald:wght@400;500&display=swap" rel="stylesheet">
<style>
:root{
  --blue:#1a6fb8;
  --blue-dark:#0c4f8c;
  --blue-deep:#083d6e;
  --green:#7cb93b;
  --text:#555c63;
  --heading:#2d4f73;
  --page:#e8edf2;
  --white:#ffffff;
}
*{box-sizing:border-box;margin:0;padding:0}
html,body{width:1200px;height:2264px;overflow:hidden}
body{background:var(--page);font-family:'Roboto',sans-serif;color:var(--text);position:relative}
.site-header{position:absolute;top:0;left:0;width:1200px;height:172px;background:linear-gradient(180deg,var(--blue-dark),var(--blue))}
.brand{position:absolute;left:132px;top:30px;display:flex;align-items:center;gap:14px}
.brand-mark{width:54px;height:54px;border-radius:50%;background:var(--green)}
.brand-name{font-family:'Oswald',sans-serif;font-size:30px;color:var(--white);letter-spacing:1px;line-height:1.05}
.header-info{position:absolute;right:132px;top:22px;text-align:right;color:var(--white)}
.header-info h1{font-family:'Oswald',sans-serif;font-weight:500;font-size:26px;letter-spacing:1px;margin-bottom:12px}
.header-info .row{display:flex;justify-content:flex-end;gap:40px;font-size:13px;margin-bottom:8px}
.header-info .row span{display:flex;align-items:center;gap:6px}
.content{position:absolute;top:172px;left:80px;width:1040px;height:1668px;background:var(--white)}
.main-nav{position:absolute;top:172px;left:132px;width:936px;height:30px;background:var(--blue-deep);display:flex;padding-left:14px}
.main-nav a{color:var(--white);text-decoration:none;font-size:14px;line-height:30px;padding:0 16px}
.main-nav a.active{background:var(--blue)}
.slider{position:absolute;top:202px;left:132px;width:936px;height:538px;background:linear-gradient(120deg,#dfe8ef 0%,#b9cfe0 45%,#8fb3d2 100%)}
.slide-caption{position:absolute;right:44px;top:150px;width:560px;background:rgba(12,79,140,.82);padding:20px 24px;color:var(--white)}
.slide-caption h2{font-family:'Oswald',sans-serif;font-size:40px;font-weight:500;letter-spacing:1px;line-height:1.2}
.slide-caption h3{font-size:26px;font-weight:400;color:#cfe6ff;margin:4px 0 12px}
.slide-caption p{font-size:13px;line-height:1.6}
.slider-arrows{position:absolute;right:12px;bottom:12px;display:flex;gap:4px}
.slider-arrows span{width:30px;height:30px;background:var(--blue-deep);display:flex;align-items:center;justify-content:center}
.intro{position:absolute;top:780px;left:132px;width:936px;text-align:center}
.intro h2{font-family:'Oswald',sans-serif;font-size:28px;font-weight:400;color:var(--heading);letter-spacing:1px}
.intro .tagline{font-style:italic;color:var(--green);font-size:17px;margin:8px 0 22px}
.body-text{font-size:13px;line-height:1.75;text-align:left}
.services{position:absolute;top:1040px;left:132px;width:936px;display:flex;justify-content:space-between}
.service{width:210px;text-align:center}
.service .icon{width:120px;height:120px;border-radius:50%;background:var(--blue);margin:0 auto 24px;display:flex;align-items:center;justify-content:center;box-shadow:0 0 0 6px #d9e8f5}
.service h4{font-size:14px;font-weight:700;color:var(--heading);letter-spacing:.5px;margin-bottom:8px}
.service p{font-size:12px;line-height:1.5}
.more-text{position:absolute;top:1290px;left:132px;width:936px}
.more-text p+p{margin-top:22px}
.features{position:absolute;top:1480px;left:132px;width:936px}
.features h2{font-family:'Oswald',sans-serif;font-size:28px;font-weight:400;color:var(--heading);text-align:center;letter-spacing:1px;margin-bottom:28px}
.feature-grid{display:flex;justify-content:space-between}
.feature{width:296px}
.feature .photo{height:180px}
.feature h5{font-size:14px;font-weight:700;color:var(--heading);margin-top:14px;text-transform:uppercase}
.site-footer{position:absolute;top:1840px;left:0;width:1200px;height:424px;background:var(--blue)}
.footer-cols{position:absolute;top:30px;left:132px;width:936px;display:flex;justify-content:space-between;color:var(--white)}
.footer-col{width:280px}
.footer-col h6{font-size:16px;font-weight:500;letter-spacing:.5px;margin-bottom:14px}
.footer-col p{font-size:13px;line-height:1.7}
.footer-col .map{height:200px;background:linear-gradient(135deg,#eef3e6,#cfe2f3)}
.contact-line{display:flex;align-items:center;gap:10px;font-size:13px;margin-bottom:14px}
.bottom-bar{position:absolute;bottom:0;left:0;width:1200px;height:50px;background:var(--blue-deep);color:#cfe2f3;font-size:12px;line-height:50px;padding-left:132px}
</style>
</head>
<body>
<header class="site-header">
  <div class="brand"><span class="brand-mark"></span><span class="brand-name">KESTREL<br>Compounding Pharmacy</span></div>
  <div class="header-info">
    <h1>KESTREL COMPOUNDING PHARMACY</h1>
    <div class="row"><span>Unit 4, 18 Harbour Road</span><span>
      <svg width="12" height="12" viewBox="0 0 24 24" fill="#fff"><path d="M6.6 10.8a15 15 0 006.6 6.6l2.2-2.2c.3-.3.7-.4 1-.2 1.1.4 2.3.6 3.6.6.6 0 1 .4 1 1V20c0 .6-.4 1-1 1A17 17 0 013 4c0-.6.4-1 1-1h3.5c.6 0 1 .4 1 1 0 1.3.2 2.5.6 3.6.1.3 0 .7-.2 1z"/></svg>08 9400 1234</span></div>
    <div class="row"><span>Eastbrook Centre, WA 6000</span><span>Fax 08 9400 1235</span></div>
    <div class="row"><span>compounding@kestrelchemist.example</span></div>
  </div>
</header>
<div class="content"></div>
<nav class="main-nav">
  <a class="active" href="#">Home</a><a href="#">About us</a><a href="#">Locations</a><a href="#">Things</a><a href="#">Contact us</a>
</nav>
<section class="slider" role="img" aria-label="Pharmacist working with a microscope in the preparation laboratory">
  <div class="slide-caption">
    <h2>COMPOUNDING PHARMACY</h2>
    <h3>Customised Medications for Patients</h3>
    <p>Each preparation is made to order in our purpose built laboratory, tailored to the dose, strength and form your prescriber and you need.</p>
  </div>
  <div class="slider-arrows">
    <span><svg width="10" height="12" viewBox="0 0 10 12"><path d="M8 1L2 6l6 5" stroke="#fff" stroke-width="2" fill="none"/></svg></span>
    <span><svg width="10" height="12" viewBox="0 0 10 12"><path d="M2 1l6 5-6 5" stroke="#fff" stroke-width="2" fill="none"/></svg></span>
  </div>
</section>
<section class="intro">
  <h2>WHAT IS COMPOUNDING PHARMACY?</h2>
  <p class="tagline">Lorem ipsum dolor sit amet, consectetur adipiscing elit, sed do eiusmod tempor incididunt</p>
  <p class="body-text">With over thirty years of service, our pharmacy has prepared personalised medicines for local families, prescribers and veterinary clinics. Compounding means a qualified pharmacist combines, mixes or alters ingredients to create a medication made for one patient. This can mean removing an allergen or dye, changing a tablet into a liquid, flavouring a dose for a child or pet, or making a strength that is not available commercially. Our dedicated preparation laboratory follows strict quality standards so every formula is accurate, consistent and safe, and our team works closely with your doctor or vet to get it right.</p>
</section>
<section class="services">
  <div class="service">
    <div class="icon"><svg width="60" height="60" viewBox="0 0 60 60"><rect x="8" y="22" width="44" height="16" rx="8" fill="#fff" transform="rotate(-35 30 30)"/></svg></div>
    <h4>DISSECTETUR ADIPISCING</h4><p>Made to order doses prepared from quality ingredients for each patient.</p>
  </div>
  <div class="service">
    <div class="icon"><svg width="60" height="60" viewBox="0 0 60 60"><circle cx="30" cy="30" r="20" fill="#fff"/><path d="M16 44L44 16" stroke="#1a6fb8" stroke-width="4"/></svg></div>
    <h4>EUISMOD TEMPOR</h4><p>Flavoured liquids and easy forms for children and pets alike.</p>
  </div>
  <div class="service">
    <div class="icon"><svg width="60" height="60" viewBox="0 0 60 60"><path d="M24 10h12v6h-2v10l12 20c1 2 0 4-2 4H16c-2 0-3-2-2-4l12-20V16h-2z" fill="#fff"/></svg></div>
    <h4>ET DOLORE MAGNA</h4><p>Purpose built laboratory with careful checks on every batch.</p>
  </div>
  <div class="service">
    <div class="icon"><svg width="60" height="60" viewBox="0 0 60 60"><path d="M24 12h12v12h12v12H36v12H24V36H12V24h12z" fill="#fff"/></svg></div>
    <h4>NOSTRUD EXERCITATION</h4><p>Working with your doctor or vet to find the right formula.</p>
  </div>
</section>
<section class="more-text body-text">
  <p>A compounding pharmacist can prepare creams, capsules, troches, drops and liquids in exact strengths. This service suits patients who cannot swallow tablets, need a dose between standard sizes, or react to fillers in regular products. We keep detailed records of each formula so repeat prescriptions are always identical.</p>
  <p>We also prepare medicines for veterinary clients, from flavoured pastes for cats to measured doses for horses. Visit our store or call our team to talk about your needs and learn how a personalised preparation could help you, your patients or your animals.</p>
</section>
<section class="features">
  <h2>FEATURE ITEMS</h2>
  <div class="feature-grid">
    <div class="feature"><div class="photo" role="img" aria-label="Laboratory glassware and equipment" style="background:linear-gradient(135deg,#c8dcec,#7fa9cc)"></div><h5>Vet article</h5></div>
    <div class="feature"><div class="photo" role="img" aria-label="Skin care treatment being applied" style="background:linear-gradient(135deg,#f1e2d8,#c9b2a4)"></div><h5>Scar therapy</h5></div>
    <div class="feature"><div class="photo" role="img" aria-label="Doctor examining a patient's thyroid" style="background:linear-gradient(135deg,#e4ecf2,#9cb8cf)"></div><h5>Thyroid extract</h5></div>
  </div>
</section>
<footer class="site-footer">
  <div class="footer-cols">
    <div class="footer-col">
      <h6>OPENING HOURS</h6>
      <p>7 DAYS A WEEK 8AM TO 8PM<br>Public holidays 9AM to 5PM</p>
      <p style="margin-top:10px">Our compounding pharmacist is available on weekdays. Please call ahead for urgent orders.</p>
    </div>
    <div class="footer-col">
      <h6>CONTACT MAP</h6>
      <div class="map" role="img" aria-label="Map showing the pharmacy location"></div>
    </div>
    <div class="footer-col">
      <h6>CONTACT US</h6>
      <div class="contact-line"><svg width="16" height="16" viewBox="0 0 24 24" fill="#fff"><path d="M6.6 10.8a15 15 0 006.6 6.6l2.2-2.2c.3-.3.7-.4 1-.2 1.1.4 2.3.6 3.6.6.6 0 1 .4 1 1V20c0 .6-.4 1-1 1A17 17 0 013 4c0-.6.4-1 1-1h3.5c.6 0 1 .4 1 1 0 1.3.2 2.5.6 3.6.1.3 0 .7-.2 1z"/></svg>08 9400 1234</div>
      <div class="contact-line"><svg width="16" height="16" viewBox="0 0 24 24" fill="#fff"><path d="M12 2a7 7 0 00-7 7c0 5 7 13 7 13s7-8 7-13a7 7 0 00-7-7zm0 9.5A2.5 2.5 0 1112 6a2.5 2.5 0 010 5.5z"/></svg>08 9400 1235</div>
      <div class="contact-line"><svg width="16" height="16" viewBox="0 0 24 24"><rect x="2" y="5" width="20" height="14" fill="#fff"/><path d="M2 5l10 8 10-8" stroke="#1a6fb8" stroke-width="2" fill="none"/></svg>compounding@kestrelchemist.example</div>
    </div>
  </div>
  <div class="bottom-bar">Copyright © 2015 Kestrel Compounding Pharmacy. Privacy policy</div>
</footer>
</body>
</html>
```